HearthMile business card and stationary design

We are looking for a simple yet elegant design for our mortgage company business card and stationary.

The card should include:
Name (Marcus Pell)
Title (CEO)
Phone Number (732-555-0182)
Address (48 Birchwell Court, Suite 314, Marlow Falls, NJ 07791)
Email (email@hearthmile.example)
"NMLS" i.e. (NMLS 61947)
"Company NMLS" (Company NMLS 274615)

Contact Information for Business Card

See above

```html
<!DOCTYPE html>
<html lang="en">
<head>
<meta charset="utf-8">
<title>HearthMile Business Card</title>
<link href="https://fonts.googleapis.com/css2?family=Montserrat:wght@400;500;600&display=swap" rel="stylesheet">
<style>
  :root {
    --backdrop: #6b6b6b;
    --navy: #1b2732;
    --navy-soft: #2c3f50;
    --sky: #29a8e0;
    --paper: #ffffff;
    --ink: #4a4f55;
    --ink-dark: #17222c;
  }
  * { margin: 0; padding: 0; box-sizing: border-box; }
  html, body {
    width: 1049px; height: 1200px; overflow: hidden;
    background: var(--backdrop);
    font-family: "Montserrat", sans-serif;
  }
  .card {
    position: absolute;
    left: 163px;
    width: 723px;
    height: 413px;
    border-radius: 24px;
    overflow: hidden;
  }
  .card-front { top: 139px; background: var(--navy); }
  .card-back { top: 646px; background: var(--paper); }

  .front-wordmark {
    position: absolute; left: 0; right: 0; top: 168px;
    text-align: center;
    font-size: 68px; font-weight: 500; letter-spacing: 0.5px;
    color: var(--navy-soft);
  }
  .front-licence {
    position: absolute; left: 0; right: 0; top: 361px;
    text-align: center;
    font-size: 18px; color: #e9eef2; letter-spacing: 0.3px;
  }
  .front-licence .dot { color: var(--sky); margin: 0 10px; }

  .edge-stripe {
    position: absolute; left: 0; top: 0; bottom: 0; width: 14px;
    background: var(--navy);
  }
  .edge-tab {
    position: absolute; left: 0; top: 177px; width: 14px; height: 56px;
    background: var(--paper);
  }
  .edge-tab::after {
    content: ""; position: absolute; left: 0; top: 6px; bottom: 6px; width: 14px;
    background: var(--sky); border-radius: 0 6px 6px 0;
  }

  .holder { position: absolute; left: 37px; top: 178px; }
  .holder-name {
    font-size: 29px; font-weight: 600; color: var(--sky); letter-spacing: 0.5px; line-height: 1;
  }
  .holder-title { margin-top: 10px; font-size: 18px; color: var(--ink); }

  .back-wordmark {
    position: absolute; right: 36px; top: 72px;
    font-size: 44px; font-weight: 500; color: var(--ink-dark); line-height: 1;
  }

  .address {
    position: absolute; left: 428px; top: 176px;
    font-size: 18px; line-height: 28px; color: var(--ink); font-style: normal;
  }
  .contacts { position: absolute; left: 428px; top: 284px; list-style: none; }
  .contacts li {
    display: flex; align-items: center; gap: 9px;
    height: 28px; font-size: 18px; color: var(--ink); white-space: nowrap;
  }
  .contacts svg { width: 16px; height: 16px; fill: var(--sky); flex: none; }
</style>
</head>
<body>
  <section class="card card-front">
    <div class="front-wordmark">HearthMile</div>
    <p class="front-licence">NMLS 61947<span class="dot">•</span>Company NMLS 274615</p>
  </section>

  <section class="card card-back">
    <div class="edge-stripe"></div>
    <div class="edge-tab"></div>

    <div class="holder">
      <p class="holder-name">MARCUS PELL</p>
      <p class="holder-title">CEO</p>
    </div>

    <div class="back-wordmark">HearthMile</div>

    <address class="address">
      48 Birchwell Court, Suite 314<br>
      Marlow Falls, NJ 07791
    </address>

    <ul class="contacts">
      <li>
        <svg viewBox="0 0 24 24" aria-hidden="true"><path d="M6.6 10.8a15.1 15.1 0 0 0 6.6 6.6l2.2-2.2a1 1 0 0 1 1-.25 11.4 11.4 0 0 0 3.6.57 1 1 0 0 1 1 1V20a1 1 0 0 1-1 1A17 17 0 0 1 3 4a1 1 0 0 1 1-1h3.5a1 1 0 0 1 1 1c0 1.25.2 2.45.57 3.6a1 1 0 0 1-.25 1z"/></svg>
        732-555-0182
      </li>
      <li>
        <svg viewBox="0 0 24 24" aria-hidden="true"><path d="M2 6h20v2l-10 6L2 8z"/><path d="M2 10l10 6 10-6v8H2z"/></svg>
        email@hearthmile.example
      </li>
      <li>
        <svg viewBox="0 0 24 24" aria-hidden="true"><circle cx="12" cy="12" r="10"/><path d="M12 2a15 15 0 0 1 0 20M12 2a15 15 0 0 0 0 20M2 12h20" stroke="#fff" stroke-width="1.4" fill="none"/></svg>
        www.hearthmile.example
      </li>
    </ul>
  </section>
</body>
</html>
```